Re-design and craft the perfect CV platform

We are building a CV-based platform designed to connect employees and employers, with a strong focus on individual users. As we're just starting out, we're looking to have our platform and logo redesigned to better reflect our vision
https://app.zelvorhire.com/
Colors like in the logo attached
#87C032 #6A6E71 #618930 - also you can add more colors if you like.
https://app.zelvorhire.com/dashboard - This page would be nice if you plan it, like personal Bio dashboard. Attached picture (Dashboard wanted) one idea from how we would like to be, but we are open for new professional ideas/solutions.
https://app.zelvorhire.com/posts - On this page we want to be showed the jobs posted. Attached one picture about our idea (jobs page wanted)
https://app.zelvorhire.com/profile - design something nice.
Only Photoshop, Illustrator or Figma
Other pictures from the app attached (as looking right now)

Target Market(s)

Job seekers, HR, Recruiters

Industry/Entity Type

HR Tech

Number of Pages Required

5+ page

Colors
00AB8E
00BBA5
67D7C9
C6EFE9
E9F9F6

```html
<!DOCTYPE html>
<html lang="en">
<head>
<meta charset="utf-8">
<title>Zelvorhire – Jobs</title>
<link href="https://fonts.googleapis.com/css2?family=Poppins:wght@400;500;600;700&display=swap" rel="stylesheet">
<style>
:root{
  --green:#87C032;
  --green-dark:#618930;
  --grey:#6A6E71;
  --ink:#55595c;
  --ink-strong:#3f4346;
  --panel:#f2f2f2;
  --panel-2:#efefef;
  --line:#dcdcdc;
  --white:#ffffff;
  --pill:#e3edd3;
  --edit-grey:#5f6366;
}
*{box-sizing:border-box;margin:0;padding:0}
html,body{width:1200px;height:712px;overflow:hidden;background:var(--white);font-family:"Poppins",sans-serif;color:var(--ink)}
.app{position:relative;width:1200px;height:712px}
.sidebar{position:absolute;left:0;top:0;width:224px;height:699px;background:var(--panel);border-bottom-right-radius:10px}
.brand{position:absolute;top:42px;left:0;width:224px;display:flex;justify-content:center;align-items:center;gap:8px;color:var(--green);font-weight:700;font-size:22px}
.brand-dot{width:16px;height:16px;border-radius:50%;background:var(--green)}
.profile-photo{position:absolute;left:43px;top:110px;width:138px;height:137px;border-radius:10px;background:linear-gradient(180deg,#c9d2da 0%,#a9b4bf 60%,#5b636d 100%)}
.profile-name{position:absolute;top:253px;width:224px;text-align:center;color:var(--green);font-weight:700;font-size:16px}
.profile-role{position:absolute;top:276px;width:224px;text-align:center;font-size:10px;color:var(--ink-strong)}
.profile-email{position:absolute;top:289px;width:224px;text-align:center;font-size:14px;font-weight:500;color:var(--ink-strong)}
.divider{position:absolute;left:17px;width:191px;height:1px;background:var(--line)}
.details{position:absolute;left:30px;top:340px;width:180px}
.details .row{display:flex;align-items:center;height:22.5px}
.details dt{width:62px;font-weight:600;font-size:11px;color:var(--ink)}
.details dd{font-size:8px;color:var(--ink-strong)}
.info-block{position:absolute;left:30px;width:180px}
.info-block h3{font-size:11.5px;font-weight:600;color:var(--ink)}
.info-block p{font-size:8.5px;color:var(--ink-strong);margin-top:2px}

.topbar{position:absolute;left:224px;top:20px;width:958px;height:71px;background:var(--panel);border-radius:0 36px 36px 0}
.page-title{position:absolute;left:25px;top:22px;font-size:18px;font-weight:700;color:var(--ink)}
.nav{position:absolute;right:13px;top:10px;display:flex;align-items:center;gap:14px}
.nav a{text-decoration:none;color:var(--ink);font-size:12px;font-weight:600;display:flex;align-items:center;gap:2px}
.bell{position:relative;margin:0 16px 0 10px}
.bell .badge{position:absolute;top:-3px;right:-4px;width:8px;height:8px;border-radius:50%;background:#e9423a}
.avatar{width:50px;height:50px;border-radius:50%;background:radial-gradient(circle at 50% 40%,#c9d89f,#9cc651)}

.toolbar{position:absolute;left:241px;top:110px;width:941px;height:56px;background:var(--panel-2);border-radius:12px}
.search{position:absolute;left:9px;top:6px;width:668px;height:44px;background:var(--white);border-radius:8px;display:flex;align-items:center;padding-left:13px;font-size:13px;color:var(--ink)}
.search-btn{position:absolute;right:7px;top:6px;width:32px;height:32px;border-radius:6px;background:var(--green);display:flex;align-items:center;justify-content:center}
.tool{position:absolute;top:6px;width:46px;height:44px;background:var(--white);border-radius:8px;display:flex;align-items:center;justify-content:center}
.tool.active{background:var(--green)}

.jobs{position:absolute;left:241px;top:178px;width:941px;height:477px;background:var(--panel-2);border-radius:12px}
.jobs-head{position:absolute;top:18px;left:0;width:100%;height:26px;font-size:12.5px;font-weight:600;color:var(--ink)}
.jobs-head span{position:absolute;top:0}
.jobs .rule{position:absolute;left:15px;width:912px;height:1.5px;background:var(--line)}
.job{position:absolute;left:0;width:100%;height:75px}
.job .logo{position:absolute;left:30px;top:14px;width:47px;height:47px;border-radius:50%;background:var(--white);box-shadow:0 2px 6px rgba(0,0,0,.08);display:flex;align-items:center;justify-content:center}
.job .logo i{width:16px;height:16px;border-radius:50%;display:block}
.job .title{position:absolute;left:88px;top:18px;font-size:13.5px;line-height:19px}
.job .title b{font-weight:500;color:var(--ink)}
.job .company{position:absolute;left:309px;top:18px;font-size:13.5px;line-height:19px}
.job .company b{font-weight:500}
.status{position:absolute;left:449px;top:25px;width:79px;height:25px;border-radius:13px;background:var(--pill);color:var(--green);font-size:9px;font-weight:700;display:flex;align-items:center;justify-content:center}
.date{position:absolute;top:28px;font-size:13px;font-weight:500}
.edit{position:absolute;left:839px;top:24px;width:69px;height:26px;border-radius:13px;background:var(--green);color:var(--white);font-size:9px;font-weight:700;display:flex;align-items:center;justify-content:center}
.edit.muted{background:var(--edit-grey)}
.footer{position:absolute;left:30px;top:439px;display:flex;align-items:center;gap:12px;font-size:13.5px;font-weight:600;color:var(--ink)}
.per-page{width:47px;height:26px;border-radius:5px;background:#e4e4e4;display:flex;align-items:center;justify-content:center;gap:2px;font-weight:500}
.pager{position:absolute;left:641px;top:439px;display:flex;gap:5.5px}
.pager span{width:27px;height:27px;border-radius:4px;background:#e4e4e4;display:flex;align-items:center;justify-content:center;font-size:13px;font-weight:500;color:var(--ink)}
.pager span.current{background:var(--green);color:var(--white)}
</style>
</head>
<body>
<div class="app">
  <aside class="sidebar">
    <div class="brand"><span class="brand-dot"></span>Zelvorhire</div>
    <div class="profile-photo" role="img" aria-label="Profile photo of Marcus Bellweather"></div>
    <div class="profile-name">MARCUS BELLWEATHER</div>
    <div class="profile-role">Software Engineer</div>
    <div class="profile-email">hello@marcusbell.com</div>
    <div class="divider" style="top:324px"></div>
    <dl class="details">
      <div class="row"><dt>Phone:</dt><dd>+01 555-214-9083</dd></div>
      <div class="row"><dt>Email:</dt><dd>hello@marcusbell.com</dd></div>
      <div class="row"><dt>Age:</dt><dd>35</dd></div>
      <div class="row"><dt>Sex:</dt><dd>Mail</dd></div>
      <div class="row"><dt>Address:</dt><dd>Some goes address here</dd></div>
    </dl>
    <div class="divider" style="top:460px"></div>
    <div class="info-block" style="top:475px"><h3>Highest level of education:</h3><p>Master's Degree in Computer Science</p></div>
    <div class="divider" style="top:523px"></div>
    <div class="info-block" style="top:538px"><h3>Work Experience:</h3><p>Years of Work Experience: 15+ years</p></div>
  </aside>

  <header class="topbar">
    <h1 class="page-title">JOBS</h1>
    <nav class="nav">
      <a href="#">JOBS<svg width="9" height="6" viewBox="0 0 9 6"><path d="M1 1l3.5 3.5L8 1" stroke="#87C032" stroke-width="1.5" fill="none"/></svg></a>
      <a href="#">CV</a>
      <span class="bell"><svg width="16" height="17" viewBox="0 0 16 17"><path d="M8 1a5 5 0 0 0-5 5v4l-2 3h14l-2-3V6a5 5 0 0 0-5-5z" fill="#6A6E71"/><circle cx="8" cy="15" r="2" fill="#6A6E71"/></svg><i class="badge"></i></span>
      <div class="avatar" role="img" aria-label="User avatar"></div>
    </nav>
  </header>

  <section class="toolbar">
    <div class="search">Enter filter keyword
      <span class="search-btn"><svg width="14" height="14" viewBox="0 0 14 14"><circle cx="6" cy="6" r="4.5" stroke="#fff" stroke-width="1.6" fill="none"/><path d="M9.5 9.5L13 13" stroke="#fff" stroke-width="1.6"/></svg></span>
    </div>
    <span class="tool" style="left:682px"><svg width="15" height="15" viewBox="0 0 15 15" fill="none" stroke="#55595c" stroke-width="1.4"><rect x="1" y="1" width="5" height="5" rx="1"/><rect x="9" y="1" width="5" height="5" rx="1"/><rect x="1" y="9" width="5" height="5" rx="1"/><rect x="9" y="9" width="5" height="5" rx="1"/></svg></span>
    <span class="tool" style="left:733px"><svg width="15" height="15" viewBox="0 0 15 15"><path d="M1.5 2h12L9 8v5l-3-1.5V8z" fill="none" stroke="#55595c" stroke-width="1.4" stroke-linejoin="round"/></svg></span>
    <span class="tool active" style="left:784px"><svg width="18" height="14" viewBox="0 0 18 14" stroke="#fff" stroke-width="1.6" fill="none"><path d="M1 2h14M1 6h14M1 10h7M10 10l2.5 2.5L17 8"/></svg></span>
    <span class="tool" style="left:835px"><svg width="16" height="16" viewBox="0 0 16 16" fill="none" stroke="#55595c" stroke-width="1.6"><path d="M13.5 8A5.5 5.5 0 1 1 11.5 3.8"/><path d="M12 1v3.5H8.5"/></svg></span>
    <span class="tool" style="left:886px"><svg width="4" height="14" viewBox="0 0 4 14" fill="#55595c"><circle cx="2" cy="2" r="1.5"/><circle cx="2" cy="7" r="1.5"/><circle cx="2" cy="12" r="1.5"/></svg></span>
  </section>

  <section class="jobs">
    <div class="jobs-head">
      <span style="left:30px">JOB POSITION</span>
      <span style="left:309px">COMPANY</span>
      <span style="left:448px">STATUS</span>
      <span style="left:570px">FOLLOW UP</span>
      <span style="left:714px">DATE APPLIED</span>
    </div>
    <div class="rule" style="top:44px"></div>

    <div class="job" style="top:45px">
      <span class="logo"><i style="background:#7c5cd6"></i></span>
      <div class="title"><b>Novaquill Systems</b><br>Digital Marketing Manager</div>
      <div class="company"><b>Orbelin Corp</b><br>US$0.00</div>
      <span class="status">BOOKMARK</span>
      <span class="date" style="left:570px">09/09/2023</span>
      <span class="date" style="left:714px">09/09/2023</span>
      <span class="edit">EDIT</span>
    </div>
    <div class="rule" style="top:121px"></div>

    <div class="job" style="top:122px">
      <span class="logo"><i style="background:#87C032"></i></span>
      <div class="title"><b>Ledgerbay Capital</b><br>Operations Manager - Logistics</div>
      <div class="company"><b>Orbelin Corp</b><br>US$0.00</div>
      <span class="status">BOOKMARK</span>
      <span class="date" style="left:570px">09/09/2023</span>
      <span class="date" style="left:714px">09/09/2023</span>
      <span class="edit muted">EDIT</span>
    </div>
    <div class="rule" style="top:197px"></div>

    <div class="job" style="top:196px">
      <span class="logo"><i style="background:#3a5ca8"></i></span>
      <div class="title"><b>Glintrock Labs</b><br>UI/UX Designer</div>
      <div class="company"><b>Orbelin Corp</b><br>US$0.00</div>
      <span class="status">BOOKMARK</span>
      <span class="date" style="left:570px">09/09/2023</span>
      <span class="date" style="left:714px">09/09/2023</span>
      <span class="edit">EDIT</span>
    </div>
    <div class="rule" style="top:272px"></div>

    <div class="job" style="top:272px">
      <span class="logo"><i style="background:#d63a3a"></i></span>
      <div class="title"><b>Streamvale Analytics</b><br>Content Marketing Specialist</div>
      <div class="company"><b>Orbelin Corp</b><br>US$0.00</div>
      <span class="status">BOOKMARK</span>
      <span class="date" style="left:570px">09/09/2023</span>
      <span class="date" style="left:714px">09/09/2023</span>
      <span class="edit muted">EDIT</span>
    </div>
    <div class="rule" style="top:348px"></div>

    <div class="job" style="top:346px">
      <span class="logo"><i style="background:#4a4e52"></i></span>
      <div class="title"><b>Skyrune Works</b><br>UX Researcher</div>
      <div class="company"><b>Orbelin Corp</b><br>US$0.00</div>
      <span class="status">BOOKMARK</span>
      <span class="date" style="left:570px">09/09/2023</span>
      <span class="date" style="left:714px">09/09/2023</span>
      <span class="edit">EDIT</span>
    </div>
    <div class="rule" style="top:422px"></div>

    <div class="footer">Result per page:
      <span class="per-page">5<svg width="8" height="5" viewBox="0 0 8 5"><path d="M1 1l3 3 3-3" stroke="#87C032" stroke-width="1.4" fill="none"/></svg></span>
    </div>
    <div class="pager">
      <span><svg width="6" height="10" viewBox="0 0 6 10"><path d="M5 1L1 5l4 4" stroke="#87C032" stroke-width="1.6" fill="none"/></svg></span>
      <span>1</span><span>2</span><span class="current">3</span><span>···</span><span>8</span><span>9</span><span>10</span>
      <span><svg width="6" height="10" viewBox="0 0 6 10"><path d="M1 1l4 4-4 4" stroke="#87C032" stroke-width="1.6" fill="none"/></svg></span>
    </div>
  </section>
</div>
</body>
</html>
```